MRT Property - Business Cards

Looking for a business card & general letterhead, signage etc design for our new logo.

Colours:
000a20
0056a2
00b5ef
0088ce
68cef2

Fonts:
Poppins
Karla

Please keep look and feel of new brand - example in the zip package I sent.

```html
<!DOCTYPE html>
<html lang="en">
<head>
<meta charset="utf-8">
<title>MRT Property – Business Cards</title>
<link href="https://fonts.googleapis.com/css2?family=Poppins:wght@400;600;700&family=Karla:wght@400;500&display=swap" rel="stylesheet">
<style>
  :root{
    --ink:#000a20;
    --navy:#0d1429;
    --royal:#0056a2;
    --cyan:#00b5ef;
    --azure:#0088ce;
    --sky:#68cef2;
    --paper:#ffffff;
    --stage:#3d3d3d;
  }
  *{margin:0;padding:0;box-sizing:border-box}
  html,body{width:1200px;height:803px;overflow:hidden;background:var(--stage)}
  .stage{position:relative;width:1200px;height:803px}
  .card{position:absolute;width:540px;height:310px;border-radius:24px;overflow:hidden}
  .card-front{left:60px;top:90px;background:var(--paper);border-bottom:3px solid var(--sky)}
  .card-back{left:600px;top:400px;background:var(--navy);border:2px solid var(--sky)}
  .front-wave{position:absolute;inset:0;width:100%;height:100%}
  .holder{position:absolute;right:36px;top:28px;text-align:right;font-family:"Poppins",sans-serif}
  .holder-name{color:var(--royal);font-weight:700;font-size:22px;line-height:1.15}
  .holder-role{color:var(--cyan);font-size:12px;font-weight:400;line-height:1.3}
  .brand{position:absolute;right:40px;top:100px;display:flex;align-items:center;gap:10px;
    font-family:"Poppins",sans-serif;font-weight:700;font-size:32px;line-height:1;color:var(--royal);letter-spacing:.5px}
  .brand-dot{width:18px;height:18px;border-radius:50%;background:var(--azure)}
  .contacts{position:absolute;left:28px;bottom:18px;color:var(--paper);font-family:"Karla",sans-serif;font-size:13px;line-height:1.45;list-style:none}
  .contacts li{display:flex;align-items:center;gap:8px}
  .contacts svg{width:11px;height:11px;fill:var(--paper);flex:none}
  .contacts .address{display:block;margin-top:4px;font-size:14px;line-height:1.35}
  .back-brand{position:absolute;left:0;right:0;top:112px;text-align:center;font-family:"Poppins",sans-serif;font-weight:700;font-size:38px;line-height:1.2;color:var(--sky)}
  .back-url{position:absolute;left:0;right:0;bottom:34px;text-align:center;font-family:"Karla",sans-serif;font-size:15px;color:var(--paper);letter-spacing:.5px}
</style>
</head>
<body>
<main class="stage">
  <section class="card card-front">
    <svg class="front-wave" viewBox="0 0 540 310" preserveAspectRatio="none" aria-hidden="true">
      <path d="M0 22 C180 182 400 222 540 252 L540 310 L0 310 Z" fill="var(--sky)"/>
      <path d="M0 26 C180 186 400 226 540 256 L540 310 L0 310 Z" fill="var(--paper)"/>
      <path d="M0 28 C180 188 400 228 540 258 L540 310 L0 310 Z" fill="var(--cyan)"/>
      <path d="M0 33 C180 193 400 233 540 263 L540 310 L0 310 Z" fill="var(--royal)"/>
    </svg>
    <div class="holder">
      <div class="holder-name">Dana Whitlow</div>
      <div class="holder-role">President</div>
    </div>
    <div class="brand"><span class="brand-dot"></span>MRT Property</div>
    <ul class="contacts">
      <li><svg viewBox="0 0 12 12"><path d="M2 1h3l1 3-2 1a7 7 0 0 0 3 3l1-2 3 1v3c-6 0-10-4-10-9z"/></svg>555-218-4407</li>
      <li><svg viewBox="0 0 12 12"><path d="M3 0h6v12H3zM4 1v9h4V1z"/></svg>555-392-1186</li>
      <li><svg viewBox="0 0 12 12"><path d="M0 2h12v8H0zM1 3l5 4 5-4z"/></svg>info@MRTproperty.com</li>
      <li><svg viewBox="0 0 12 12"><circle cx="6" cy="6" r="5.5"/></svg>www.MRTproperty.com</li>
      <li class="address">412 Harbor View Road<br>Halifax, Canada 48210</li>
    </ul>
  </section>

  <section class="card card-back">
    <div class="back-brand">MRT Property</div>
    <div class="back-url">www.MRTproperty.com</div>
  </section>
</main>
</body>
</html>
```